Brandwyn Fuel Retro Website Design

Have a logo. Need a website design to go along with the logo design. Full Design Specs are here: https://files.plinverdocs.net/sheet/d/8QmRtZxWv3-41pk527LNB_XY4HaPcOdsuw2K-rb6/view

Target Market(s)

Independent Gas Station Owners

Number of Pages Required

1 page

Font styles to use
Sans Serif

Colors

Designer to choose colors to be used in the design.

```html
<!DOCTYPE html>
<html lang="en">
<head>
<meta charset="utf-8">
<title>Brandwyn Fuel</title>
<link href="https://fonts.googleapis.com/css2?family=Alfa+Slab+One&family=Bitter:wght@400&family=Lato:wght@400;700&display=swap" rel="stylesheet">
<style>
:root{
  --red:#e3242b;
  --ink:#111;
  --text:#666;
  --paper:#f4f4f2;
  --sand:#e8e6d5;
  --card:#d9d7bd;
  --white:#fff;
  --footer:#5b5b5b;
}
*{box-sizing:border-box;margin:0;padding:0}
html,body{width:1200px;height:3417px;overflow:hidden}
body{font-family:'Lato',sans-serif;color:var(--text);background:var(--paper);position:relative}
.display{font-family:'Alfa Slab One',serif;color:var(--ink);font-weight:400}
.btn{display:inline-block;background:var(--red);color:var(--white);font-family:'Alfa Slab One',serif;font-size:19px;border-radius:26px;width:157px;height:52px;line-height:52px;text-align:center;text-decoration:none}
.socials{display:flex;gap:8px}
.socials span{width:40px;height:40px;border-radius:50%;background:#eee;border:2px solid #ccc}
.socials span.primary{background:var(--red);border-color:var(--red)}

/* header */
.site-header{position:absolute;top:0;left:0;width:1200px;height:93px;background:var(--white);border-top:5px solid var(--red);z-index:3}
.nav{position:absolute;top:37px;font-size:15px;letter-spacing:.5px;display:flex;gap:38px;color:#888;text-transform:uppercase}
.nav a{color:#888;text-decoration:none}
.nav a.active{color:var(--red)}
.nav.left{left:79px}
.nav.right{left:741px;gap:42px}
.site-header .socials{position:absolute;right:77px;top:24px}
.brand-tab{position:absolute;left:511px;top:20px;width:178px;height:146px;background:var(--white);border-radius:0 0 89px 89px;display:flex;align-items:center;justify-content:center;z-index:4}
.brand-tab span{font-family:'Alfa Slab One',serif;font-size:19px;color:var(--ink);text-align:center;line-height:1.1}

/* hero */
.hero{position:absolute;top:93px;left:0;width:1200px;height:626px;background:linear-gradient(180deg,#a9a8a3 0%,#8f8d87 45%,#6e6b63 80%,#5d5a52 100%);text-align:center}
.hero h1{position:absolute;top:190px;width:100%;font-size:112px;color:#ececec;line-height:1}
.hero .est{position:absolute;top:340px;width:100%;font-size:88px;color:#ececec;line-height:1}

/* about */
.about{position:absolute;top:719px;left:0;width:1200px;height:510px;text-align:center}
.about .mark{position:absolute;left:560px;top:64px;width:80px;height:80px;border-radius:50%;background:var(--red);border:5px solid var(--white);box-shadow:0 3px 6px rgba(0,0,0,.2)}
.about h2{position:absolute;top:162px;width:100%;font-size:46px}
.about p{position:absolute;left:265px;top:238px;width:670px;font-size:14.5px;line-height:26px}
.about .btn{position:absolute;left:522px;top:396px}

/* services */
.services{position:absolute;top:1229px;left:0;width:1200px;height:676px;background:var(--sand)}
.services h2{position:absolute;top:60px;width:100%;text-align:center;font-size:46px}
.cards{position:absolute;left:77px;top:157px;display:flex;gap:13px}
.card{width:252px;height:457px;background:var(--card);text-align:center;position:relative;box-shadow:0 1px 3px rgba(0,0,0,.12)}
.card .photo{position:absolute;left:31px;top:30px;width:190px;height:190px;border-radius:50%;border:3px solid #555}
.card h3{position:absolute;top:246px;width:100%;font-family:'Bitter',serif;font-weight:400;font-size:24px;color:var(--ink)}
.card p{position:absolute;top:290px;left:12px;width:228px;font-size:14px;line-height:23px}
.card .btn{position:absolute;left:47px;top:375px}

/* containers */
.containers{position:absolute;top:1905px;left:0;width:1200px;height:561px}
.containers .frame{position:absolute;left:103px;top:64px;width:417px;height:372px;border:17px solid var(--red)}
.containers .photo{position:absolute;left:77px;top:105px;width:493px;height:300px;background:linear-gradient(160deg,#b7b9bc,#8e9196 60%,#6f7277);clip-path:polygon(0 20%,70% 0,100% 12%,100% 100%,65% 100%,0 78%)}
.containers h2{position:absolute;left:627px;top:60px;font-size:46px}
.containers .copy{position:absolute;left:627px;top:130px;width:465px;font-size:14.5px;line-height:26px}
.containers .copy p+p{margin-top:16px}
.containers .btn{position:absolute;left:625px;top:450px}

/* career */
.career{position:absolute;top:2466px;left:0;width:1200px;height:159px;background:var(--card)}
.career h2{position:absolute;left:80px;top:52px;font-size:46px}
.career p{position:absolute;left:301px;top:50px;width:590px;font-size:14.5px;line-height:26px}
.career .btn{position:absolute;left:967px;top:53px}

/* contact */
.contact{position:absolute;top:2625px;left:0;width:1200px;height:686px;background:linear-gradient(180deg,#9a9a98,#b9b8b4 55%,#a7a6a2)}
.contact h2{position:absolute;top:60px;width:100%;text-align:center;font-size:46px}
.contact .panel{position:absolute;left:156px;top:155px;width:888px;height:469px;background:rgba(100,100,100,.75)}
.info,.form{position:absolute;top:31px;width:397px;height:406px;background:var(--white)}
.info{left:32px;padding:26px 25px}
.form{left:459px;padding:21px 26px}
.info .brand{font-family:'Alfa Slab One',serif;font-size:18px;color:var(--ink);display:flex;align-items:center;gap:10px;margin-bottom:36px}
.info .brand i{width:28px;height:28px;border-radius:50%;background:var(--red);display:block}
.item{position:relative;padding-left:39px;margin-bottom:24px}
.item svg{position:absolute;left:0;top:2px}
.item h4{font-family:'Bitter',serif;font-weight:400;color:var(--red);font-size:16px;margin-bottom:8px}
.item p{font-size:14.5px;line-height:27px}
.field{height:57px;background:#f3f3f3;border:1px solid #ddd;border-radius:3px;margin-bottom:11px;padding:18px 12px;font-size:13.5px;color:#555}
.field.tall{height:92px}
.form .send{display:inline-block;background:var(--red);color:var(--white);font-size:19px;width:156px;height:57px;line-height:57px;text-align:center;border-radius:29px;margin-top:0}

/* footer */
.site-footer{position:absolute;top:3311px;left:0;width:1200px;height:106px;background:var(--footer);color:#eee;font-family:'Bitter',serif;font-size:14px}
.site-footer p{position:absolute;left:79px;top:45px}
.site-footer b{font-family:'Alfa Slab One',serif;font-weight:400}
.site-footer .socials{position:absolute;right:77px;top:33px}
</style>
</head>
<body>

<header class="site-header">
  <nav class="nav left"><a class="active">Home</a><a>About</a><a>Services</a><a>Containers</a></nav>
  <nav class="nav right"><a>Careers</a><a>Contact</a></nav>
  <div class="socials"><span class="primary"></span><span></span><span></span></div>
</header>
<div class="brand-tab"><span>BRANDWYN<br>FUEL</span></div>

<section class="hero" role="img" aria-label="Vintage sepia photo of the early fuel depot with delivery trucks and storage tanks">
  <h1 class="display">BRANDWYN FUEL</h1>
  <div class="est display">EST 1966</div>
</section>

<section class="about">
  <div class="mark"></div>
  <h2 class="display">ABOUT BRANDWYN FUEL</h2>
  <p>Lorem ipsum dolor sit amet, consectetur adipiscing elit, sed do eiusmod tempor incididunt ut labore et dolore magna aliqua. Ut enim ad minim veniam, quis nostrud exercitation ullamco laboris nisi ut aliquip ex ea commodo consequat. Duis aute irure dolor in reprehenderit in voluptate velit esse cillum dolore eu fugiat nulla pariatur. Excepteur sint occaecat cupidatat non proident, sunt in culpa qui officia deserunt mollit anim id est laborum.</p>
  <a class="btn">READ MORE</a>
</section>

<section class="services">
  <h2 class="display">OUR SERVICES</h2>
  <div class="cards">
    <article class="card">
      <div class="photo" role="img" aria-label="Fuel delivery trucks parked outdoors" style="background:linear-gradient(180deg,#c9ccd0,#9a9a95 55%,#6f6c62)"></div>
      <h3>Fuel Delivery</h3>
      <p>Brandwyn Fuel provides fuel delivery for independent gas stations, convenience stores.</p>
      <a class="btn">READ MORE</a>
    </article>
    <article class="card">
      <div class="photo" role="img" aria-label="Store shelves stocked with oil bottles" style="background:linear-gradient(180deg,#8a6a4a,#4d6f8f 50%,#7a4a3a)"></div>
      <h3>Oil</h3>
      <p>Looking for speciality auto, tractor, tractor trailer, aviation or other commercial oils.</p>
      <a class="btn">READ MORE</a>
    </article>
    <article class="card">
      <div class="photo" role="img" aria-label="White farm fuel tank" style="background:linear-gradient(160deg,#f2f2f2,#dadada 60%,#8e8a80)"></div>
      <h3>Farm Fuel</h3>
      <p>Looking for gasoline, diesel red diesel off road fuel or farm diesel? We can deliver.</p>
      <a class="btn">READ MORE</a>
    </article>
    <article class="card">
      <div class="photo" role="img" aria-label="Grey storage container" style="background:linear-gradient(180deg,#c4c6c8,#9a9da1 60%,#6d6a5f)"></div>
      <h3>Cargo Containers</h3>
      <p>Want to purchase or lease a storage container, we have what you need!</p>
      <a class="btn">READ MORE</a>
    </article>
  </div>
</section>

<section class="containers">
  <div class="frame"></div>
  <div class="photo" role="img" aria-label="Grey steel shipping container"></div>
  <h2 class="display">CONTAINERS</h2>
  <div class="copy">
    <p>Lorem ipsum dolor sit amet, consectetur adipiscing elit, sed do eiusmod tempor incididunt ut labore et dolore magna aliqua. Ut enim ad minim veniam, quis nostrud exercitation ullamco laboris nisi ut aliquip ex ea commodo consequat. Duis aute irure dolor in reprehenderit in voluptate velit esse cillum dolore eu fugiat nulla pariatur. Excepteur sint occaecat cupidatat non proident, sunt in culpa qui officia deserunt mollit anim id est laborum.</p>
    <p>Lorem ipsum dolor sit amet, consectetur adipiscing elit, sed do eiusmod tempor incididunt ut labore et dolore magna aliqua. Ut enim ad minim veniam, quis nostrud exercitation.</p>
  </div>
  <a class="btn">READ MORE</a>
</section>

<section class="career">
  <h2 class="display">CAREER</h2>
  <p>Lorem ipsum dolor sit amet, consectetur adipiscing elit, sed do eiusmod tempor incididunt ut labore et dolore magna aliqua. Ut enim ad minim veniam.</p>
  <a class="btn">READ MORE</a>
</section>

<section class="contact" role="img" aria-label="Faded photo of a fuel tanker truck in the background">
  <h2 class="display">CONTACT US</h2>
  <div class="panel">
    <div class="info">
      <div class="brand"><i></i>BRANDWYN FUEL</div>
      <div class="item">
        <svg width="18" height="22" viewBox="0 0 18 22"><path d="M9 1a7 7 0 0 0-7 7c0 5 7 13 7 13s7-8 7-13a7 7 0 0 0-7-7z" fill="none" stroke="#e3242b" stroke-width="2.5"/><circle cx="9" cy="8" r="2.5" fill="#e3242b"/></svg>
        <h4>BRANDWYN FUEL</h4>
        <p>123, Address, State Name<br>City, Street, Zipcode</p>
      </div>
      <div class="item">
        <svg width="20" height="20" viewBox="0 0 20 20"><path d="M4 1l4 4-2 3c1 3 3 5 6 6l3-2 4 4-3 3C8 19 1 12 1 4z" fill="#e3242b"/></svg>
        <h4>Telephone</h4>
        <p>123-456-7890</p>
      </div>
      <div class="item">
        <svg width="22" height="16" viewBox="0 0 22 16"><rect x="1" y="1" width="20" height="14" fill="none" stroke="#e3242b" stroke-width="2"/><path d="M1 1l10 8 10-8" fill="none" stroke="#e3242b" stroke-width="2"/></svg>
        <h4>Email Address</h4>
        <p>info@brandwynfuel.com</p>
      </div>
    </div>
    <form class="form">
      <div class="field">Name :</div>
      <div class="field">Email :</div>
      <div class="field">Phone :</div>
      <div class="field tall">Message / comments :</div>
      <span class="send">READ MORE</span>
    </form>
  </div>
</section>

<footer class="site-footer">
  <p>Copyright © <b>BRANDWYN FUEL</b> - 2018 . All Right Reserved</p>
  <div class="socials"><span class="primary"></span><span></span><span></span></div>
</footer>

</body>
</html>
```